Business Card Design for Varomir Facility Services

We are looking for a Business Card Design for the Company "Varomir Facility Services."
Front side:
- Company Logo (small)
- Company Name, address, pohone, website and personal data.
- white background, for text e.g. company colors (blue or green like in the logo)
Please use following data:
Company data:
Varomir Facility Services Kostelac
Birkenhaldweg 14
6342 Seldwil
www.varomir-fs.ch
Person data:
Tarik Kostelac
Geschäftsführer
+41 76 519 47 83
info@varomir-fs.ch
Back side:
could be colored in blue or green
please use a big logo sing and some smaller icons to say what is all beeing offered in facility services, like cleaning, maintenance cleaning
industrial cleaning, caretaking, gardening, disposal. There is no need for everyone of the icons if there are similar or an icon is standing for more of them.
colors to use:
blue: HEX 246BB0
green: HEX 52B33E

```html
<!DOCTYPE html>
<html lang="de">
<head>
<meta charset="utf-8">
<title>Varomir Facility Services – Visitenkarte</title>
<link rel="stylesheet" href="https://fonts.googleapis.com/css2?family=Montserrat:wght@400;500;600&display=swap">
<style>
  :root {
    --brand-blue: #246BB0;
    --brand-green: #52B33E;
    --card-white: #ffffff;
    --card-black: #151617;
    --map-tone: #2a2c2e;
    --text-grey: #6b6f73;
    --stage: #3a3433;
  }
  * { box-sizing: border-box; margin: 0; padding: 0; }
  html, body { width: 1200px; height: 716px; overflow: hidden; }
  body {
    background: var(--stage);
    font-family: "Montserrat", Arial, sans-serif;
    position: relative;
  }
  .card {
    position: absolute;
    top: 205px;
    width: 520px;
    height: 306px;
    border-radius: 6px;
    overflow: hidden;
    box-shadow: 0 10px 30px rgba(0,0,0,.45);
  }
  /* Back side */
  .card-back { left: 50px; background: var(--card-black); }
  .card-back .world-map {
    position: absolute; inset: 24px 30px;
    border-radius: 40px;
    background: radial-gradient(ellipse at 50% 50%, var(--map-tone) 0%, rgba(42,44,46,.4) 60%, transparent 80%);
  }
  .card-back .brand {
    position: absolute; left: 0; right: 0; top: 50%;
    transform: translateY(-50%);
    display: flex; align-items: center; justify-content: center; gap: 14px;
  }
  .brand-dot { width: 22px; height: 22px; border-radius: 50%; background: var(--brand-blue); flex: none; }
  .brand-name {
    color: var(--brand-blue);
    font-weight: 600;
    font-size: 30px;
    line-height: 1.05;
    letter-spacing: .04em;
    text-transform: uppercase;
  }
  .brand-name small { display: block; font-size: 15px; letter-spacing: .18em; }

  /* Front side */
  .card-front { left: 630px; background: var(--brand-blue); }
  .card-front .swoosh { position: absolute; inset: 0; }
  .person { position: absolute; left: 185px; top: 26px; }
  .person-name { color: var(--brand-blue); font-weight: 600; font-size: 17px; }
  .person-role { color: var(--text-grey); font-size: 12px; margin-top: 2px; }
  .contact {
    position: absolute; left: 26px; top: 162px;
    list-style: none; color: var(--card-white); font-size: 13px;
  }
  .contact li { display: flex; align-items: center; gap: 7px; margin-bottom: 4px; }
  .contact svg { width: 11px; height: 11px; flex: none; }
  .card-front .brand {
    position: absolute; right: 26px; top: 108px;
    display: flex; align-items: center; gap: 10px;
  }
  .card-front .brand-name { font-size: 24px; text-align: right; }
  .card-front .brand-name small { font-size: 12px; }
  .address {
    position: absolute; right: 28px; bottom: 16px;
    color: var(--card-white); font-size: 15px; text-align: right; line-height: 1.35;
  }
</style>
</head>
<body>

<section class="card card-back" aria-label="Rückseite">
  <div class="world-map" role="img" aria-label="Dezente Weltkarte im Hintergrund"></div>
  <div class="brand">
    <span class="brand-dot"></span>
    <p class="brand-name">Varomir<small>Facility Services</small></p>
  </div>
</section>

<section class="card card-front" aria-label="Vorderseite">
  <svg class="swoosh" viewBox="0 0 520 306" preserveAspectRatio="none" aria-hidden="true">
    <path d="M140 0 L520 0 L520 240 C370 222 185 176 104 88 C82 58 92 20 140 0 Z" fill="var(--brand-green)"/>
    <path d="M158 0 L520 0 L520 228 C385 210 205 168 128 88 C108 58 118 22 158 0 Z" fill="var(--card-white)"/>
  </svg>

  <div class="person">
    <p class="person-name">Tarik Kostelac</p>
    <p class="person-role">Geschäftsführer</p>
  </div>

  <ul class="contact">
    <li>
      <svg viewBox="0 0 24 24" fill="currentColor"><path d="M6.6 10.8a15.1 15.1 0 0 0 6.6 6.6l2.2-2.2c.3-.3.7-.4 1-.2 1.1.4 2.3.6 3.6.6.6 0 1 .4 1 1V20c0 .6-.4 1-1 1A17 17 0 0 1 3 4c0-.6.4-1 1-1h3.5c.6 0 1 .4 1 1 0 1.3.2 2.5.6 3.6.1.3 0 .7-.2 1z"/></svg>
      +41 76 519 47 83
    </li>
    <li>
      <svg viewBox="0 0 24 24" fill="none" stroke="currentColor" stroke-width="2"><rect x="3" y="5" width="18" height="14" rx="1"/><path d="M3 6l9 7 9-7"/></svg>
      info@varomir-fs.ch
    </li>
    <li>
      <svg viewBox="0 0 24 24" fill="none" stroke="currentColor" stroke-width="2"><circle cx="12" cy="12" r="9"/><path d="M3 12h18M12 3c3 3 3 15 0 18M12 3c-3 3-3 15 0 18"/></svg>
      www.varomir-fs.ch
    </li>
  </ul>

  <div class="brand">
    <span class="brand-dot"></span>
    <p class="brand-name">Varomir<small>Facility Services</small></p>
  </div>

  <p class="address">Birkenhaldweg 14<br>6342 Seldwil</p>
</section>

</body>
</html>
```